Custom Seed Packet design for Flower Farm

We need a design for our seeds packets.
The design will be a kind of "fill in the blanks" as we need the design to be adaptable for multiple varieties of seed. We will be using the design for a rubber stamp.
Our seed packets are 90x90mm in size.
Black logo only. No colour required.
A vintage botanical influence is desired.
Will need to include the following info,
"Wrenfield Gable Co logo" , "Seeds", "Plant Type", "Variety", "Harvested"

```html
<!DOCTYPE html>
<html lang="en">
<head>
<meta charset="utf-8">
<title>Seed Packet – Wrenfield Gable Co</title>
<link href="https://fonts.googleapis.com/css2?family=Pinyon+Script&family=Open+Sans:wght@400;600&display=swap" rel="stylesheet">
<style>
  :root {
    --page: #ffffff;
    --kraft: #d8c29c;
    --kraft-edge: #cdb58c;
    --ink: #1e1b17;
    --leaf: #a99878;
    --bracket: #6e655a;
  }
  * { box-sizing: border-box; margin: 0; padding: 0; }
  html, body {
    width: 1122px; height: 1200px; overflow: hidden;
    background: var(--page);
  }
  .canvas { position: relative; width: 1122px; height: 1200px; }

  .packet {
    position: absolute; left: 175px; top: 200px;
    width: 711px; height: 872px;
    background: var(--kraft);
    border: 1px solid var(--kraft-edge);
  }
  .label-frame {
    position: absolute; left: 57px; top: 118px;
    width: 586px; height: 577px;
    border: 2px solid var(--ink);
    outline: 1px solid var(--ink);
    outline-offset: -8px;
  }
  .sprig {
    position: absolute;
    background: linear-gradient(135deg, var(--leaf), var(--kraft));
    opacity: .85; border-radius: 4px;
  }
  .sprig--tl { left: 14px; top: 14px; width: 160px; height: 112px; }
  .sprig--tr { right: 14px; top: 14px; width: 100px; height: 196px; }
  .sprig--bl { left: 14px; bottom: 14px; width: 118px; height: 250px; }
  .sprig--br { right: 14px; bottom: 14px; width: 106px; height: 250px; }

  .seeds-title {
    position: absolute; left: 0; right: 0; top: 42px;
    text-align: center;
    font-family: "Pinyon Script", cursive;
    font-weight: 400;
    font-size: 72px; color: var(--ink); line-height: 1;
  }
  .brand-block {
    position: absolute; left: 140px; top: 146px;
    width: 312px; height: 176px;
    display: flex; align-items: center; justify-content: center;
  }
  .bracket { position: absolute; top: 0; width: 14px; height: 176px; border: 3px solid var(--bracket); }
  .bracket--left { left: 0; border-right: none; }
  .bracket--right { right: 0; border-left: none; }
  .brand-name {
    font-family: "Open Sans", sans-serif; font-weight: 600;
    font-size: 22px; color: var(--ink); letter-spacing: .3px;
  }

  .fields { position: absolute; left: 142px; top: 350px; width: 306px; }
  .field {
    display: flex; align-items: flex-end; height: 40px;
    font-family: "Open Sans", sans-serif; font-size: 14px; color: var(--ink);
  }
  .field .line { flex: 1; border-bottom: 1px solid var(--ink); margin-left: 4px; height: 14px; }

  .brand-mark {
    position: absolute; left: 880px; top: 1100px; width: 200px;
    font-family: "Open Sans", sans-serif; font-weight: 600;
    font-size: 19px; color: var(--ink); text-align: center;
  }
</style>
</head>
<body>
<div class="canvas">
  <div class="packet">
    <div class="label-frame">
      <div class="sprig sprig--tl" role="img" aria-label="Botanical sprig with leaves and berries"></div>
      <div class="sprig sprig--tr" role="img" aria-label="Botanical sprig with leaves"></div>
      <div class="sprig sprig--bl" role="img" aria-label="Botanical sprig with leaves"></div>
      <div class="sprig sprig--br" role="img" aria-label="Botanical sprig with leaves and berries"></div>

      <h1 class="seeds-title">Seeds</h1>

      <div class="brand-block">
        <span class="bracket bracket--left"></span>
        <span class="brand-name">Wrenfield Gable Co</span>
        <span class="bracket bracket--right"></span>
      </div>

      <div class="fields">
        <div class="field">Plant Type<span class="line"></span></div>
        <div class="field">Variety<span class="line"></span></div>
        <div class="field">Harvested<span class="line"></span></div>
      </div>
    </div>
  </div>

  <div class="brand-mark">Wrenfield Gable Co</div>
</div>
</body>
</html>
```